Business Card Design

Hi I need a business card designed, we already have the business name logo artwork and would like some concept ideas for the Bus Card layout.
On the back of the card i want to include the products and services that we offer.
We are a Plastics Sheeting manufacture based in Perth Australia.

                                       

We need a BC design for a company called Tarvo Plastics based in Perth Australia.

We supply from DIY to Trade & Industrial  Engineering Markets.

We specialise in:

·         Cut to size panels  (all shapes and sizes)

·         Plastics fabrication & Welding

·         Custom Designs

·         Plastic Repairs

·         PVC Pipe Slotting & PVC Pipe Threading

·         Supplier of all types of engineering plastics and profiles.

Including:           Acrylic / Clarvene

                               Polycarbonate / Dorvil

                               Prismatic Light Diffuser

                               Vantrib

                               HDPE / UHMWPE

                               PVC / PVC Foam

                               Nylon

                               HIPS

```html
<!DOCTYPE html>
<html lang="en">
<head>
<meta charset="utf-8">
<title>Tarvo Plastics – Business Card</title>
<link href="https://fonts.googleapis.com/css2?family=Open+Sans:wght@400;600;700;800&display=swap" rel="stylesheet">
<style>
  :root {
    --navy: #1b2f6e;
    --orange: #f0891e;
    --text: #3b3b3b;
    --rule: #c9c9c9;
    --card: #ffffff;
    --backdrop: #e9e6e1;
  }
  * { box-sizing: border-box; margin: 0; padding: 0; }
  html, body { width: 1200px; height: 720px; overflow: hidden; }
  body {
    background: var(--backdrop);
    font-family: "Open Sans", Arial, sans-serif;
    color: var(--text);
    position: relative;
  }
  .card {
    position: absolute;
    width: 540px;
    height: 320px;
    background: var(--card);
    border-radius: 6px;
    box-shadow: 0 6px 18px rgba(0,0,0,.15);
    overflow: hidden;
  }
  .card--front { left: 40px; top: 130px; }
  .card--back  { left: 620px; top: 250px; }

  .brand {
    font-weight: 800;
    color: var(--navy);
    letter-spacing: -0.5px;
    display: flex;
    align-items: center;
    gap: 10px;
    white-space: nowrap;
  }
  .brand__mark {
    width: 14px; height: 14px;
    background: var(--orange);
    flex: none;
  }

  /* Front */
  .card--front .brand { position: absolute; left: 34px; top: 32px; font-size: 44px; }
  .name-block { position: absolute; right: 34px; top: 108px; text-align: right; }
  .name-block__name { font-weight: 700; color: var(--navy); font-size: 18px; line-height: 1.1; }
  .name-block__title { color: var(--orange); font-size: 12px; }
  .tab { position: absolute; background: var(--orange); border-radius: 6px; }
  .tab--right { right: -6px; top: 106px; width: 14px; height: 42px; }
  .tab--left { left: -6px; top: 172px; width: 16px; height: 118px; }
  .contact { position: absolute; left: 30px; top: 170px; font-size: 12.5px; line-height: 17.5px; }
  .contact li { list-style: none; display: flex; align-items: center; gap: 7px; white-space: nowrap; }
  .contact svg { width: 13px; height: 13px; flex: none; }

  /* Back */
  .card--back .brand { position: absolute; left: 0; right: 0; top: 26px; justify-content: center; font-size: 40px; }
  .headline {
    position: absolute; left: 0; right: 0; top: 92px;
    text-align: center; color: var(--navy); font-weight: 700; font-size: 13.5px; line-height: 1.3;
  }
  .columns { position: absolute; left: 28px; right: 22px; top: 140px; display: flex; }
  .col h3 { color: var(--navy); font-weight: 700; font-size: 16px; margin-bottom: 3px; white-space: nowrap; }
  .col--services { width: 282px; flex: none; padding-right: 12px; }
  .col--materials { flex: 1; padding-left: 16px; border-left: 1px solid var(--rule); min-height: 150px; }
  .bullets li {
    list-style: none; font-size: 12px; line-height: 17px;
    position: relative; padding-left: 13px;
  }
  .col--materials .bullets li { white-space: nowrap; }
  .bullets li::before {
    content: ""; position: absolute; left: 0; top: 6px;
    width: 6px; height: 6px; border-radius: 50%; background: var(--orange);
  }
  .bullets .pair { display: flex; gap: 8px; padding-left: 0; }
  .bullets .pair::before { display: none; }
  .bullets .pair span { position: relative; padding-left: 13px; white-space: nowrap; }
  .bullets .pair span::before {
    content: ""; position: absolute; left: 0; top: 6px;
    width: 6px; height: 6px; border-radius: 50%; background: var(--orange);
  }
</style>
</head>
<body>

<section class="card card--front" aria-label="Business card front">
  <div class="brand"><span class="brand__mark"></span>Tarvo Plastics</div>
  <div class="name-block">
    <div class="name-block__name">Your Name</div>
    <div class="name-block__title">Title</div>
  </div>
  <span class="tab tab--right"></span>
  <span class="tab tab--left"></span>
  <ul class="contact">
    <li><svg viewBox="0 0 16 16"><circle cx="8" cy="8" r="8" fill="#f0891e"/><path d="M5 4.5l1.8-.5 1 2.2-1 .8a5 5 0 0 0 2.2 2.2l.8-1 2.2 1-.5 1.8C8 11.3 4.7 8 5 4.5z" fill="#fff"/></svg>08 5550 2011</li>
    <li><svg viewBox="0 0 16 16"><circle cx="8" cy="8" r="8" fill="#f0891e"/><rect x="5.5" y="3.5" width="5" height="9" rx="1" fill="#fff"/><rect x="6.5" y="5" width="3" height="5" fill="#f0891e"/></svg>0400 555 789</li>
    <li><svg viewBox="0 0 16 16"><circle cx="8" cy="8" r="8" fill="#f0891e"/><rect x="4" y="7" width="8" height="5" rx="1" fill="#fff"/><rect x="5.5" y="4" width="5" height="3" fill="#fff"/></svg>08 5550 2022</li>
    <li><svg viewBox="0 0 16 16"><circle cx="8" cy="8" r="8" fill="#f0891e"/><rect x="4" y="5" width="8" height="6" fill="#fff"/><path d="M4 5l4 3.5L12 5" stroke="#f0891e" fill="none"/></svg>sales@tarvoplastics.com.au</li>
    <li>Unit 4/18 Marlow Circuit Brennard WA 6160</li>
    <li>PO Box 2210 Brennard DC WA 6972</li>
    <li>Kestrel Holdings Pty Ltd T/A Tarvo Plastics ABN: TBA</li>
  </ul>
</section>

<section class="card card--back" aria-label="Business card back">
  <div class="brand"><span class="brand__mark"></span>Tarvo Plastics</div>
  <p class="headline">The Products And Services That We Offer<br>Are Supplied From Diy To Trade &amp; Industrial Engineering Markets</p>
  <div class="columns">
    <div class="col col--services">
      <h3>We specialise in:</h3>
      <ul class="bullets">
        <li>Cut to size panels (all shapes and sizes)</li>
        <li>Plastics fabrication &amp; Welding</li>
        <li>Custom Designs</li>
        <li>Plastic Repairs</li>
        <li>PVC Pipe Slotting &amp; PVC Pipe Threading</li>
        <li>Supplier of all types of engineering plastics and profiles</li>
      </ul>
    </div>
    <div class="col col--materials">
      <h3>Including:</h3>
      <ul class="bullets">
        <li>Acrylic / Clarvene</li>
        <li>Polycarbonate / Dorvil</li>
        <li>Prismatic Light Diffuser</li>
        <li class="pair"><span>Vantrib</span><span>HDPE / UHMWPE</span></li>
        <li>PVC / PVC Foam</li>
        <li class="pair"><span>Nylon</span><span>HIPS</span></li>
      </ul>
    </div>
  </div>
</section>

</body>
</html>
```